Corwin Beacon Lighting - Commercial & Residential Landscape Lighting

Landscape Lighting Services & Design: Create a website for our landscape lighting company. We would like the design to be tailored around this description:
Illuminate with Confidence. Designed with Precision. Installed with Care.
Locally and veteran-owned, we take pride in transforming outdoor spaces through innovative lighting solutions tailored to your vision. From landscape and holiday lighting to permanent installations, our effortless process and expert design deliver breathtaking results and lasting curb appeal. Backed by a lifetime warranty and quarterly service options, our commitment to quality and customer satisfaction is unwavering. Try before you buy and experience your home in a whole new light with our complimentary demo kit — see the stunning effects before you decide.
- Also, add in this information as well; Outdoor Lighting not only beautifies spaces but also significantly enhances safety by illuminating your home or business. Beautifully lit entrances deter potential intruders, making your home a safer place for your loved ones. we also offer quarterly service plans to ensure lighting equipment continues to operate & illuminate effectively throughout the year. Also mention we provide free estimates and we are offering a 10% discount to military, veterans, and first responders.

Target Market(s)

Luxury market

Industry/Entity Type

Landscape Lighting - Residential & Commercial Lighting Services

Coding

Coded - Design and coding required

Number of Pages Required

2 page

Colors
00AB8E
00BBA5
67D7C9
C6EFE9
E9F9F6
59FF00
82FF00
B8FF75
E3FFCB
F4FFEA
FFC000
F8CF3A
FAE287
FDF2CF
FEFAEE

Requirements
Must have
• a lead generation button where people can submit their information for us to reach out to them and schedule their free estimate, homepage, about page, contact page, products and services page, user friendly, easy to navigate, and it also must be engaging and eye popping, as well as appealing to the luxury market. Please use colors; verdent green, dark green, ivory, and sunny yellow. Also, include an about page that references our story; Derek is retired Army and he opened a fitness studio in 2017 with his wife Jolene. He has installed low voltage lighting in every home he lived in and for his friends and family over the years and decided to open his own business because he is passionate about beautifying outdoor landscapes and highlighting a properties full potential, not only in the day but at night as well all while providing safety and security for his clients. Having a deep respect for nature and landscaping, he wants to provide the same care and quality to each of his clients as he has in the fitness industry for decades. He believes small businesses are the back bone of America and he's excited to provide a service that is all to often neglected in the design of a home.
Nice to have
• I would like to have a clear intent and purpose, engaging web design, clear call to action, optimized for search engines, mobile friendy design, security measures, credibility indicators

```html
<!DOCTYPE html>
<html lang="en">
<head>
<meta charset="utf-8">
<title>Corwin Beacon Lighting – Commercial &amp; Residential Landscape Lighting</title>
<link href="https://fonts.googleapis.com/css2?family=Roboto:wght@300;400;500;700&family=Poppins:wght@400;500;600;700&display=swap" rel="stylesheet">
<style>
:root{
  --dark-green:#1c3a1b;
  --verdant:#2c6a31;
  --sunny:#fdd22f;
  --sunny-soft:#fde27a;
  --ivory:#f6f2e9;
  --white:#ffffff;
  --ink:#1a1a1a;
  --field:#f4f4f4;
  --field-line:#dedede;
}
*{margin:0;padding:0;box-sizing:border-box}
html,body{width:1200px;height:4971px;overflow:hidden}
body{position:relative;font-family:"Poppins",sans-serif;color:var(--ink);background:var(--white)}
.abs{position:absolute}
.photo{position:absolute}
.btn{position:absolute;display:flex;align-items:center;justify-content:center;background:var(--sunny);color:var(--dark-green);font-family:"Poppins",sans-serif;font-weight:600;font-size:13px;border-radius:4px 12px 4px 12px;text-transform:uppercase;letter-spacing:.2px}
.eyebrow{position:absolute;left:0;width:1200px;text-align:center;font-family:"Roboto",sans-serif;font-weight:400;font-size:26px;color:var(--verdant)}
.section-title{position:absolute;left:0;width:1200px;text-align:center;font-family:"Roboto",sans-serif;font-weight:500;font-size:39px;color:var(--dark-green)}

/* Hero */
.hero{position:absolute;left:0;top:0;width:1200px;height:515px;overflow:hidden;
  background:linear-gradient(90deg,#1b3419 0%,#1f3b1d 32%,#3b4a2a 55%,#6c5a34 72%,#3a4226 88%,#24361d 100%)}
.hero-glow{position:absolute;left:520px;top:0;width:680px;height:515px;
  background:radial-gradient(ellipse at 55% 45%,rgba(240,190,110,.45),rgba(0,0,0,0) 60%)}
.brand{position:absolute;font-family:"Roboto",sans-serif;font-weight:400;color:var(--sunny);letter-spacing:1px;line-height:1}
.nav{position:absolute;top:44px;left:444px;display:flex;gap:0;font-size:14px;color:var(--white)}
.nav a{position:absolute;white-space:nowrap;text-decoration:none;color:var(--white)}
.nav .active{font-weight:600}
.hero-line{position:absolute;left:112px;font-family:"Roboto",sans-serif;font-weight:300;font-size:37px;color:var(--white);line-height:1}
.hero-line b{font-weight:700}
.btn-hero{left:112px;top:359px;width:177px;height:39px;background:var(--verdant);color:var(--white);font-size:13px;border-radius:4px 12px 4px 12px}
.badge-halo{position:absolute;left:939px;top:351px;width:224px;height:224px;border-radius:50%;background:rgba(253,210,47,.55)}
.badge{position:absolute;left:951px;top:363px;width:200px;height:200px;border-radius:50%;background:var(--sunny);text-align:center;color:var(--dark-green)}
.badge .pct{position:absolute;top:38px;left:0;width:200px;font-family:"Poppins",sans-serif;font-weight:700;font-size:36px;line-height:1}
.badge .pct small{font-size:16px}
.badge .off{position:absolute;top:82px;left:0;width:200px;font-weight:700;font-size:18px}
.badge .who{position:absolute;top:112px;left:30px;width:140px;font-size:13.5px;line-height:16px}

/* About */
.about{position:absolute;left:0;top:515px;width:1200px;height:1034px;background:var(--ivory)}
.about-head{position:absolute;left:558px;font-family:"Roboto",sans-serif}
.about-copy{position:absolute;left:559px;top:743px;width:545px;font-size:14.6px;line-height:25.8px;color:#2a2a2a}
.safety-copy{position:absolute;left:114px;top:1096px;width:386px;font-size:14.6px;line-height:25.8px;color:#2a2a2a}
.safety-copy b{font-weight:700;color:var(--ink)}
.frame-line{position:absolute;border:11px solid var(--dark-green)}

/* Services */
.card{position:absolute;top:1792px;width:479px;height:426px;background:var(--dark-green);color:var(--white)}
.card .pic{position:absolute;left:0;top:0;width:479px;height:206px}
.card h3{position:absolute;left:28px;top:251px;font-family:"Roboto",sans-serif;font-weight:500;font-size:23px}
.card .rule{position:absolute;left:28px;top:293px;width:145px;height:3px;background:var(--sunny)}
.card p{position:absolute;left:28px;top:320px;width:420px;font-size:14px;line-height:26px}

/* Story */
.story-copy{position:absolute;left:110px;top:2515px;width:464px;font-size:14.6px;line-height:25.8px;color:#2a2a2a}
.story-copy b{font-weight:700;color:var(--ink)}

/* Projects */
.projects{position:absolute;left:0;top:3019px;width:1200px;height:878px;background:var(--ivory)}

/* Contact */
.contact-frame{position:absolute;left:123px;top:4049px;width:952px;height:517px;border:12px solid var(--verdant)}
.frame-gap{position:absolute;left:424px;top:4040px;width:352px;height:30px;background:var(--white)}
.field{position:absolute;background:var(--field);border:1px solid var(--field-line);border-radius:5px;font-size:14px;color:#6a6a6a;padding:18px 0 0 26px}

/* Footer */
.footer{position:absolute;left:0;top:4655px;width:1200px;height:316px;background:var(--dark-green);color:var(--white)}
.foot-col{position:absolute;top:61px;font-size:14.5px}
.foot-col h4{font-family:"Poppins",sans-serif;font-weight:600;font-size:15px;margin-bottom:12px;letter-spacing:.3px}
.foot-col li{list-style:none;line-height:27.5px}
.contact-list li{display:flex;align-items:flex-start;gap:14px}
.contact-list svg{flex:0 0 14px;margin-top:7px}
.foot-rule{position:absolute;left:112px;top:225px;width:976px;height:1px;background:rgba(255,255,255,.25)}
.copyright{position:absolute;left:0;top:258px;width:1200px;text-align:center;font-size:14px}
</style>
</head>
<body>

<!-- Hero -->
<header class="hero">
  <div class="photo" role="img" aria-label="Stone home at dusk with warm landscape lighting along a curved paver walkway" style="left:0;top:0;width:1200px;height:515px;background:linear-gradient(90deg,#1b3419 0%,#1f3b1d 34%,#3f4b2b 55%,#725d36 72%,#3d4527 88%,#243a1e 100%)"></div>
  <div class="hero-glow"></div>
  <div class="photo" style="left:0;top:0;width:640px;height:515px;background:linear-gradient(90deg,rgba(27,52,25,.95),rgba(27,52,25,0))"></div>

  <div class="brand" style="left:112px;top:38px;font-size:26px">Corwin Beacon</div>
  <div class="brand" style="left:112px;top:68px;font-size:10px;letter-spacing:2.4px">CORWIN BEACON LIGHTING</div>

  <nav class="nav">
    <a class="active" style="left:0">Home</a>
    <a style="left:83px">About</a>
    <a style="left:167px">Products and Services</a>
    <a style="left:374px">Contact</a>
  </nav>
  <div class="btn" style="left:914px;top:35px;width:174px;height:42px">Book Free Demo</div>

  <h1>
    <span class="hero-line" style="top:176px">Illuminate with <b>Confidence.</b></span>
    <span class="hero-line" style="top:228px">Designed with <b>Precision.</b></span>
    <span class="hero-line" style="top:280px">Installed with <b>Care.</b></span>
  </h1>
  <div class="btn btn-hero">Book Free Demo</div>

  <div class="badge-halo"></div>
  <div class="badge">
    <div class="pct">10<small>%</small></div>
    <div class="off">DISCOUNT</div>
    <div class="who">Military, veterans, and first responders.</div>
  </div>
</header>

<!-- About -->
<section class="about">
  <div class="photo" role="img" aria-label="Technician installing a landscape light in a garden bed at dusk" style="left:114px;top:95px;width:382px;height:428px;background:linear-gradient(160deg,#5d6b5a 0%,#2e3a2c 45%,#1e2619 75%,#3a3220 100%)"></div>
</section>
<div class="about-head" style="top:636px;font-size:27px;font-weight:400;color:var(--verdant)">ABOUT US</div>
<h2 class="about-head" style="top:668px;font-size:39px;font-weight:500;color:var(--dark-green)">CORWIN BEACON LIGHTING</h2>
<p class="about-copy">Locally and veteran-owned, we take pride in transforming outdoor spaces through innovative lighting solutions tailored to your vision. From landscape and holiday lighting to permanent installations, our effortless process and expert design deliver breathtaking results and lasting curb appeal. Backed by a lifetime warranty and quarterly service options, our commitment to quality and customer satisfaction is unwavering. Try before you buy and experience your home in a whole new light with our complimentary demo kit — see the stunning effects before you decide.</p>

<p class="safety-copy"><b>Outdoor Lighting not only beautifies spaces but also significantly enhances safety by illuminating your home or business.</b><br>Beautifully lit entrances deter potential intruders, making your home a safer place for your loved ones. we also offer quarterly service plans to ensure lighting equipment continues to operate &amp; illuminate effectively throughout the year.</p>
<div class="btn" style="left:114px;top:1331px;width:281px;height:44px">Schedule Free Estimates</div>

<div class="frame-line" style="left:631px;top:1115px;width:490px;height:316px"></div>
<div class="photo" role="img" aria-label="Modern two-storey house glowing with exterior lighting at sunset" style="left:525px;top:1080px;width:565px;height:318px;background:linear-gradient(180deg,#7c7aa0 0%,#d79a6a 30%,#6e5a42 55%,#3c4a2a 80%,#2c3a22 100%)"></div>

<!-- Services -->
<div class="eyebrow" style="top:1669px">WHAT WE DO</div>
<h2 class="section-title" style="top:1700px">CORWIN BEACON SERVICES</h2>

<article class="card" style="left:112px">
  <div class="pic" role="img" aria-label="Commercial building with lit landscaping at night" style="background:linear-gradient(180deg,#46505e 0%,#5a4a3c 45%,#9a6a3a 65%,#2c2a22 100%)"></div>
  <h3>Commercial Landscape Lighting</h3>
  <div class="rule"></div>
  <p>Sed ut perspiciatis unde omnis iste natus luptatecusan tium doloremque laudantium, totam rem</p>
</article>
<article class="card" style="left:610px">
  <div class="pic" role="img" aria-label="Modern hillside residence with lit steps and garden at night" style="background:linear-gradient(180deg,#2a3b5a 0%,#4a5b72 40%,#8a8068 60%,#223022 100%)"></div>
  <h3>Residential Landscape Lighting</h3>
  <div class="rule"></div>
  <p>Sed ut perspiciatis unde omnis iste natus luptatecusan tium doloremque laudantium, totam rem</p>
</article>

<!-- Story -->
<div class="eyebrow" style="top:2365px">OUR STORY</div>
<h2 class="section-title" style="top:2396px">BEGINNING OF CORWIN BEACON</h2>
<p class="story-copy"><b>Derek is retired Army and he opened a fitness studio in 2017 with his wife Jolene.</b><br>He has installed low voltage lighting in every home he lived in and for his friends and family over the years and decided to open his own business because he is passionate about beautifying outdoor landscapes and highlighting a proper­ties full potential, not only in the day but at night as well all while providing safety and security for his clients. Having a deep respect for nature and landscaping, he wants to provide the same care and quality to each of his clients as he has in the fitness</p>
<div class="btn" style="left:110px;top:2832px;width:177px;height:44px">Learn More</div>

<div class="frame-line" style="left:731px;top:2550px;width:388px;height:371px"></div>
<div class="photo" role="img" aria-label="Garden path bollard lights glowing beside ornamental grasses" style="left:642px;top:2508px;width:446px;height:372px;background:linear-gradient(180deg,#1f2a1a 0%,#33462a 40%,#5a6a3a 65%,#2a2a1c 100%)"></div>

<!-- Projects -->
<section class="projects"></section>
<div class="eyebrow" style="top:3137px">OUR WORK</div>
<h2 class="section-title" style="top:3168px">FEATURED PROJECTS</h2>

<div class="frame-line" style="left:212px;top:3491px;width:297px;height:294px;border-width:12px;border-color:var(--verdant)"></div>
<div class="photo" role="img" aria-label="Brick home with lit front garden at dusk" style="left:114px;top:3279px;width:307px;height:469px;background:linear-gradient(180deg,#3a4a6a 0%,#2a3040 40%,#6a4a32 62%,#253020 100%)"></div>
<div class="photo" role="img" aria-label="House and lawn under evening lighting" style="left:442px;top:3279px;width:318px;height:224px;background:linear-gradient(180deg,#2a3428 0%,#3a3a30 45%,#7a6240 60%,#4a5a38 100%)"></div>
<div class="photo" role="img" aria-label="Lit house front and walkway at twilight" style="left:442px;top:3524px;width:318px;height:224px;background:linear-gradient(180deg,#3a4660 0%,#2c3446 40%,#8a7050 62%,#2a3424 100%)"></div>
<div class="photo" role="img" aria-label="Brick home with lit shrubs and wide lawn at dusk" style="left:781px;top:3279px;width:307px;height:469px;background:linear-gradient(180deg,#4a5a5a 0%,#3a4030 35%,#8a6238 52%,#5a5a28 70%,#3a4a1c 100%)"></div>

<!-- Contact -->
<div class="contact-frame"></div>
<div class="frame-gap"></div>
<div class="eyebrow" style="top:4028px">CONTACT US</div>
<h2 class="section-title" style="top:4059px">GET IN TOUCH</h2>
<form>
  <div class="field" style="left:274px;top:4157px;width:652px;height:54px">Full Name</div>
  <div class="field" style="left:274px;top:4232px;width:314px;height:54px">Phone Number</div>
  <div class="field" style="left:610px;top:4232px;width:316px;height:54px">Email ID</div>
  <div class="field" style="left:274px;top:4306px;width:652px;height:108px">Message</div>
  <div class="btn" style="left:459px;top:4445px;width:280px;height:43px">Schedule Free Estimates</div>
</form>

<!-- Footer -->
<footer class="footer">
  <div class="brand" style="left:112px;top:70px;font-size:38px;color:var(--white)">Corwin Beacon</div>
  <div class="brand" style="left:112px;top:118px;font-size:12px;letter-spacing:3px;color:var(--white)">CORWIN BEACON LIGHTING</div>

  <div class="foot-col" style="left:384px">
    <h4>QUICK LINKS</h4>
    <ul><li>Home</li><li>Products and Services</li><li>About Us</li></ul>
  </div>
  <div class="foot-col" style="left:638px">
    <h4>OTHER LINKS</h4>
    <ul><li>Contact Us</li><li>Terms of Service</li><li>Privacy Policy</li></ul>
  </div>
  <div class="foot-col" style="left:868px">
    <h4>CONTACT US</h4>
    <ul class="contact-list">
      <li><svg width="14" height="14" viewBox="0 0 14 14"><path d="M7 1a4 4 0 0 0-4 4c0 3 4 8 4 8s4-5 4-8a4 4 0 0 0-4-4zm0 5.5A1.5 1.5 0 1 1 7 3.5a1.5 1.5 0 0 1 0 3z" fill="#fff"/></svg><span>Corwin Beacon,<br>120 Lantern Way</span></li>
      <li><svg width="14" height="14" viewBox="0 0 14 14"><path d="M3 1l2.5 2.5-1.3 1.8a8 8 0 0 0 4.5 4.5l1.8-1.3L13 11l-1.6 2C6 13 1 8 1 2.6z" fill="#fff"/></svg><span>+1 888-555-0142</span></li>
      <li><svg width="14" height="14" viewBox="0 0 14 14"><rect x="1" y="3" width="12" height="8" rx="1" fill="#fff"/><path d="M1.5 3.5 7 7.5l5.5-4" stroke="#1c3a1b" stroke-width="1.2" fill="none"/></svg><span>info@corwinbeacon.com</span></li>
    </ul>
  </div>
  <div class="foot-rule"></div>
  <div class="copyright">© 2025 Corwin Beacon. All Rights Reserved.</div>
</footer>

</body>
</html>
```